Website for a financial survey consultancy

WHO WE ARE
We're a niche HR consultancy specialising in salary comparison surveys for the financial asset management industry. We position ourselves as a small, highly responsive organisation with a strong personal relationship with each of our 50+ blue-chip clients.

WHAT WE DO
Our business is 80% surveys (= products), 20% consultancy (= services). The surveys are a set of online products which clients interact with to find the information they are interested in.

WHAT WE WANT
We are completely revising our existing marketing website and need a new up-to-date look and feel for the site. We want you to design 2 web pages
- Home page
- Internal content page

More details below in Must Have Priorities.

REFERENCE SITES
- www.veltramoor.com - nice background image
- www.plimweather.com - ignoring the animations
- www.gasketvale.com
- www.quorbin.com - clean, fresh, styly but prob not corporate enough
- www.dulveropinex.com - spacious, beautiful, slightly dated tho
- www.tambly.co.uk - ignore the colours. Like the simplicity, larger font size (although want to stick with sans-serif fonts for main content)

DELIVERABLES
The final designs should be delivered as one or more PSD files with clearly named layers. All design elements and treatments should be separated out, for example use adjustment layers rather than applied (and subsequently irreversible) adjustments, strokes, shading, etc.

WHAT NEXT
I'll be monitoring the contest every day and can respond to questions fast. You can IM me on Chatterlyne or QBX.

Reason: Hi folks,

I am extending the deadline to this project as I am travelling this week and therefore will not be able to make a final decision until next Monday. I will try and provide further feedback over the course of this week but I am only going to be online occasionally so be prepared to wait a few days for a reply from me.

Thanks for all the designs so far.

Tobias

Target Market(s)

In order of importance, most important first

1. Potential customers - UK & US financial industry HR professionals, short on time. Heard about us already, want to find out more about what we do, confirm relevance for their needs. Core goal - establish credibility: are we properly resourced, will we be around for years to come, are we *real*.

2. Existing customers - UK & US financial industry professionals, short on time, under pressure, want results quickly, minimum faff, expect high quality, slickly presented information. Primary action: login and use surveys.

3. Industry professionals/researchers - probably arriving through blog content, looking to browse and hoover information. Valuable for their ability to spread awareness of who we are amongst their peers.

Industry/Entity Type

Financial

Requirements
Must have
• GENERAL
Style cues - Corporate, professional, financial, stylish, slick, clean, spacious, light
Size - standard 960px grid

NAVIGATION
- [ Home | About us | Surveys | Consulting | Blog ]
- Sub-nav (roll-over dropdown) on About Us, Surveys & Consulting

ALL PAGES
- Site navigation
- Client login (on screen permanently or link to ajaxy in-page pop-up)
- Footer section
- Existing logo (attached)* - this is obviously an important reference point in the design, esp colour

HOME PAGE
- Communicate (link thru to?) survey/consulting split
- Large photo(s)/backdrop (2-3 interchangeable options ideally). Please consider what rights agreement will be necessary for any photos you include in your design.
- Possibly bigger more prominent version of logo
- Strap line/sentence - "Focussed data is the key to success"
- 3 recent blog posts (should look good with and without blog post images)
- Free downloadable PDF research report + supporting blurb

INTERNAL PAGE
- Page title
- Content - typical page will be less than one screenfull
- Level 1 sub-heading
- Level 2 sub-heading
- Bulleted list
- Content supporting image (any image will do - interested in placement, borders (if any), spacing, caption, etc)
- 'Do something' button

* Note: there is some internal debate about this logo at the moment. Some (me) are keen for it to change, some (not me!) are not. If you have an web page design idea/concept that requires an evolution of the logo, go ahead and evolve it. We can explore this further in the design process as necessary, but don't sweat it.
Nice to have
• Values to communicate
- Knowledgeable
- Professional
- Secure
- Personal
- Experienced
- Financial industry specific
- Accurate
- Reliable
Should not have
• - Search box
- Social media links, other than RSS feed button (discrete)

```html
<!DOCTYPE html>
<html lang="en">
<head>
<meta charset="utf-8">
<title>Varlo — Focussed data is the key to success</title>
<link rel="stylesheet" href="https://fonts.googleapis.com/css2?family=Alegreya+Sans:ital,wght@0,400;0,500;1,400&family=Arimo:wght@400&display=swap">
<style>
:root{
  --page:#eff0ec;
  --band:#5e0000;
  --brand:#6a0a0a;
  --panel:#f5f5f4;
  --ink:#2e2e2e;
  --muted:#6a6a6a;
  --rule:#c8c8c4;
  --accent:#a51515;
  --link:#2f7fd8;
  --foot:#9a9a9a;
}
*{margin:0;padding:0;box-sizing:border-box}
html,body{width:1200px;height:712px;overflow:hidden}
body{background:var(--page);font-family:"Alegreya Sans",sans-serif;color:var(--ink);position:relative}
.hero-band{position:absolute;left:0;top:74px;width:1200px;height:264px;background:var(--band)}
.brand-panel{position:absolute;left:133px;top:0;width:193px;height:338px;background:var(--panel);box-shadow:0 0 6px rgba(0,0,0,.35);z-index:2}
.brand-name{position:absolute;left:0;width:193px;top:140px;text-align:center;font-size:50px;font-weight:400;line-height:56px;color:var(--brand)}
.client-login{position:absolute;right:151px;top:10px;font-size:15px;font-style:italic;color:#222;text-decoration:none}
.main-nav{position:absolute;left:667px;top:42px;height:32px;display:flex;border:1px solid var(--band);border-bottom:none;background:var(--page)}
.main-nav a{display:flex;align-items:center;justify-content:center;height:31px;font-size:17px;font-style:italic;color:var(--muted);text-decoration:none;border-left:1px solid var(--band)}
.main-nav a:first-child{border-left:none;color:#111}
.nav-home{width:70px}.nav-about{width:86px}.nav-surveys{width:82px}.nav-consulting{width:99px}.nav-blog{width:53px}
.strapline{position:absolute;left:326px;top:160px;width:345px;height:74px;background:linear-gradient(90deg,rgba(255,255,255,.42),rgba(255,255,255,.12) 70%,rgba(255,255,255,0));color:#fff;font-size:30px;line-height:35px;padding:4px 0 0 37px}
.split-link{position:absolute;top:295px;width:154px;height:43px;border-radius:10px 10px 0 0;background:linear-gradient(180deg,#3a0000,#520000);color:#fff;font-size:23px;display:flex;align-items:center;justify-content:center;text-decoration:none}
.split-surveys{left:366px}
.split-consulting{left:529px}
.hero-photo{position:absolute;left:748px;top:74px;width:254px;height:264px;background:radial-gradient(ellipse at 50% 75%,#d9dcd8 0,#9a9a9a 35%,#6d2424 70%,#5e0000 100%)}
.intro{position:absolute;left:133px;top:377px;width:600px;font-size:23px;line-height:32.6px;font-style:italic;color:var(--ink);white-space:nowrap}
.report-button{position:absolute;left:133px;top:559px;width:269px;height:48px;border:1px solid #cfcfcf;border-radius:4px;background:linear-gradient(180deg,#fff,#e6e4e2);text-decoration:none;display:flex;align-items:center}
.report-icon{width:39px;height:39px;margin:0 10px 0 6px;background:linear-gradient(180deg,#d42020,#8e0c0c);border-radius:2px}
.report-title{display:block;font-size:15px;font-style:italic;color:#444;line-height:17px}
.report-sub{display:block;font-size:13px;font-style:italic;color:#7a0f0f;line-height:15px}
.latest-blog{position:absolute;left:784px;top:378px;width:271px}
.latest-blog h2{font-size:16.5px;font-weight:400;font-style:italic;color:var(--accent);letter-spacing:1px;padding-bottom:4px;border-bottom:1px solid var(--rule)}
.post{font-family:"Arimo",Arial,sans-serif;font-size:11.5px;line-height:17px;color:#222;padding:5px 2px 11px;border-bottom:1px solid var(--rule)}
.post+.post{padding-top:11px}
.post:last-child{border-bottom:none}
.post time{display:block;color:var(--link);text-decoration:underline}
.site-footer{position:absolute;left:133px;top:619px;width:922px;border-top:1px solid var(--rule);padding-top:12px;display:flex;justify-content:space-between;font-family:"Arimo",Arial,sans-serif;font-size:11.5px;color:var(--foot)}
.site-footer a{color:var(--foot);text-decoration:none}
</style>
</head>
<body>
<div class="hero-band"></div>

<header class="brand-panel">
  <div class="brand-name">Varlo</div>
</header>

<a class="client-login" href="#">Client login</a>
<nav class="main-nav">
  <a class="nav-home" href="#">Home</a>
  <a class="nav-about" href="#">About us</a>
  <a class="nav-surveys" href="#">Surveys</a>
  <a class="nav-consulting" href="#">Consulting</a>
  <a class="nav-blog" href="#">Blog</a>
</nav>

<p class="strapline">Focussed data is the key<br>to success</p>
<a class="split-link split-surveys" href="#">Surveys</a>
<a class="split-link split-consulting" href="#">Consulting</a>
<div class="hero-photo" role="img" aria-label="Photo of a smiling businessman in a grey suit holding a globe"></div>

<p class="intro">It is a long established fact that a reader will be distracted by the<br>readable content of a page when looking at its layout. The point<br>of using Lorem Ipsum is that it has a more-or-less normal distri-<br>bution of letters, as opposed to using 'Content here, content<br>here', making it look like readable English</p>

<a class="report-button" href="#">
  <span class="report-icon"></span>
  <span><span class="report-title">Research report + supporting blurb</span><span class="report-sub">Free downloadable PDF</span></span>
</a>

<aside class="latest-blog">
  <h2>LATEST BLOG</h2>
  <div class="post">fact that a reader will be distracted by the readable<br>fact that a reader will be distracted<time>9:53 AM Fabruary 1, 2011</time></div>
  <div class="post">fact that a reader will be distracted by the readable<br>fact that a reader will be distracted<time>9:53 AM Fabruary 1, 2011</time></div>
  <div class="post">fact that a reader will be distracted by the readable<br>fact that a reader will be distracted<time>9:53 AM Fabruary 1, 2011</time></div>
</aside>

<footer class="site-footer">
  <span>© 2011 Varlo, Inc. All rights reserved.</span>
  <span><a href="#">Terms and Conditions</a> | <a href="#">Privacy Policy</a> || <a href="#">Business Continuity</a></span>
</footer>
</body>
</html>
```